Harborview Estates Business Card for Apartment Buildings

Create business cards for resident managers who run apartment buildings. The audience is the public who are searching for apartment rentals, and current residents who live at the apartment building. Key design element will be incorporating the company logo, however, the logo cannot dominate. The building name and manager name are more important than the logo. Current business card design leaves little room for copy, so we may need to reduce the size on the current card to allow for more space for copy.

Target Market(s)

Adults 18-65 years of age, who are looking for an apartment rental, plus current residents who live at our apartment buildings.

Industry/Entity Type

Property Management

Contact Information for Business Card

A major design element will be use of the company logo. Important property and manager contact information must be part of the design. The size of the logo will need to be reduced to make room for building and manager contact copy.

Font styles to use
Sans Serif

Colors
3176b5
000000
959595
ffffff

Requirements
Must have
• 1) Incorporate the company logo.
• 2) Use the company colors (dark blue, black/grey, over white).
• 3) FEATURE THE BUILDING NAME
• 4) FEATURE THE MANAGER NAME
• 5) The company name is less important than BUILDING and MANAGER
• 6) Manager contact information
• **SEE ATTACHED CREATIVE BRIEF**
Nice to have
• 1) Back of card logo watermark
• 2) Ability to write notes on back of carfd
Should not have
• Avoid letting the company logo dominate the card, the building name and manager are more important than the company logo.

```html
<!DOCTYPE html>
<html lang="en">
<head>
<meta charset="utf-8">
<title>Harborview Estates – Resident Manager Business Card</title>
<link href="https://fonts.googleapis.com/css2?family=Source+Sans+3:wght@400;600;700&display=swap" rel="stylesheet">
<style>
  :root {
    --brand-blue: #1a6aa8;
    --brand-grey: #454547;
    --text-grey: #555555;
    --rule-grey: #959595;
    --card-white: #f5f5f5;
    --backdrop: #2b2b2b;
  }
  * { margin: 0; padding: 0; box-sizing: border-box; }
  html, body {
    width: 1200px; height: 960px; overflow: hidden;
    background: var(--backdrop);
    font-family: "Source Sans 3", "Helvetica Neue", Arial, sans-serif;
  }
  .stage { position: relative; width: 1200px; height: 960px; }

  .card {
    position: absolute;
    width: 600px; height: 342px;
    background: var(--card-white);
    box-shadow: 0 3px 8px rgba(0,0,0,.55);
    overflow: hidden;
  }
  .card--front { left: 314px; top: 113px; }
  .card--back  { left: 311px; top: 472px; }

  /* Front: company name in the brand area */
  .front-brand {
    position: absolute; left: 28px; top: 40px;
    width: 270px; height: 270px;
    display: flex; align-items: center; justify-content: center;
  }
  .front-brand__ring {
    position: absolute; inset: 0;
    border: 10px solid var(--brand-grey);
    border-radius: 50%;
  }
  .front-brand__name {
    position: relative;
    font-size: 30px; font-weight: 700; line-height: 1.1;
    color: var(--brand-grey); text-align: center; letter-spacing: .5px;
  }

  .front-info {
    position: absolute; right: 34px; top: 44px;
    text-align: right;
  }
  .building-name {
    font-size: 21px; font-weight: 700; color: var(--brand-blue);
    line-height: 1.2;
  }
  .building-address {
    margin-top: 14px;
    font-size: 13.5px; color: var(--text-grey); line-height: 18px;
    font-style: normal;
  }
  .manager-name {
    margin-top: 27px;
    font-size: 21px; font-weight: 700; color: var(--brand-blue);
    line-height: 1.2;
  }
  .manager-role {
    font-size: 13.5px; font-weight: 600; color: var(--brand-grey);
    line-height: 18px;
  }
  .contact-list {
    list-style: none; margin-top: 28px;
  }
  .contact-list li {
    display: flex; justify-content: flex-end; align-items: center;
    font-size: 13.5px; color: var(--text-grey);
    height: 19.4px;
  }
  .contact-list svg {
    width: 14px; height: 14px; margin-left: 8px; flex: none;
    fill: var(--brand-blue);
  }

  /* Back */
  .back-brand {
    position: absolute; left: 0; right: 0; top: 40px;
    display: flex; justify-content: center; align-items: center; gap: 10px;
  }
  .back-brand__dot {
    width: 40px; height: 40px; border-radius: 50%;
    background: var(--brand-blue);
  }
  .back-brand__name {
    font-size: 26px; font-weight: 700; color: var(--brand-blue);
    letter-spacing: 1px;
  }
  .back-watermark {
    position: absolute; left: 143px; top: 6px;
    width: 330px; height: 330px; border-radius: 50%;
    border: 12px solid rgba(69,69,71,.05);
  }
  .note-line {
    position: absolute; left: 39px; width: 521px; height: 0;
    border-top: 1.5px solid var(--rule-grey);
  }
</style>
</head>
<body>
<div class="stage">

  <section class="card card--front" aria-label="Business card front">
    <div class="front-brand">
      <div class="front-brand__ring"></div>
      <div class="front-brand__name">HARBORVIEW<br>ESTATES</div>
    </div>

    <div class="front-info">
      <h1 class="building-name">Cedar Court Apartments</h1>
      <address class="building-address">4825 Linden Avenue<br>Riverside, CA 92501</address>
      <h2 class="manager-name">Marisol Delgado</h2>
      <p class="manager-role">Resident Manager</p>
      <ul class="contact-list">
        <li>555-210-4471
          <svg viewBox="0 0 16 16" aria-label="Office phone"><path d="M3.5 1l2.5 3-1.5 1.6c.8 1.9 2.2 3.3 4 4.2L10 8.3l3 2.4-1.2 2.6C7 13.5 2.4 8.8 2 4z"/></svg></li>
        <li>555-384-9026
          <svg viewBox="0 0 16 16" aria-label="Mobile phone"><path d="M4.5 1h7v14h-7zM6 3v9h4V3zm1.3 10v1h1.4v-1z" fill-rule="evenodd"/></svg></li>
        <li>555-672-1830
          <svg viewBox="0 0 16 16" aria-label="Fax"><path d="M4 1h6l2 2v3H4zM1 7h14v6h-2v2H3v-2H1zm4 4v2.5h6V11z" fill-rule="evenodd"/></svg></li>
        <li>marisol@harborviewest.com
          <svg viewBox="0 0 16 16" aria-label="Email"><path d="M1 3h14v10H1zm1.5 1.3v.4L8 8.5l5.5-3.8v-.4zM2.5 6.3v5.2h11V6.3L8 10z" fill-rule="evenodd"/></svg></li>
        <li>www.harborviewest.com
          <svg viewBox="0 0 16 16" aria-label="Website"><circle cx="8" cy="8" r="7"/><path d="M5 4c2 0 2 2 4 2s1 3-1 3-1 3-3 2S3 5 5 4z" fill="#fff"/></svg></li>
      </ul>
    </div>
  </section>

  <section class="card card--back" aria-label="Business card back">
    <div class="back-watermark"></div>
    <div class="back-brand">
      <span class="back-brand__dot"></span>
      <span class="back-brand__name">HARBORVIEW ESTATES LLC</span>
    </div>
    <div class="note-line" style="top:161px"></div>
    <div class="note-line" style="top:210px"></div>
    <div class="note-line" style="top:258px"></div>
    <div class="note-line" style="top:306px"></div>
  </section>

</div>
</body>
</html>
```